Request for Business Card Design

Hi. My name is Marlene, I am looking for a new business card design for my company, Quarrow Signal Instruments, LLC. I really like the design you did for Tarsel Venture and was hoping you could do something similar using our full logo and our mark. I am also open to any raised texture design using our mark. I have attached our full logo, which would need to be somewhere on the card, as well as the mark in both outline and full form, as well as our brand colors / guide. The card does not have to be white, as long as our logo and mark appear. I actually like darker colored business cards more, but am open to all options. If you are interested in working with me, please let me know. We would also take the business card design into letterhead design if you can do that.

```html
<!DOCTYPE html>
<html lang="en">
<head>
<meta charset="utf-8">
<title>Quarrow Signal Instruments — Business Card</title>
<link href="https://fonts.googleapis.com/css2?family=Barlow:wght@400;500;600;700&display=swap" rel="stylesheet">
<style>
  :root {
    --bg: #d9d9d9;
    --card-dark-1: #626060;
    --card-dark-2: #231f20;
    --band-dark: #3a3a3b;
    --brand-blue: #1b8db0;
    --brand-blue-light: #4ab3d4;
    --paper: #ececec;
    --ink: #2b2b2b;
    --white: #ffffff;
  }
  * { margin: 0; padding: 0; box-sizing: border-box; }
  html, body {
    width: 1200px; height: 1200px; overflow: hidden;
    background: var(--bg);
    font-family: "Barlow", Arial, sans-serif;
  }
  .card {
    position: absolute;
    left: 160px;
    width: 880px; height: 503px;
    border-radius: 32px;
    overflow: hidden;
    box-shadow: 0 14px 30px rgba(0,0,0,0.25);
  }
  .card--front {
    top: 60px;
    background: linear-gradient(115deg, var(--card-dark-1) 0%, var(--card-dark-2) 60%);
    display: flex; align-items: center; justify-content: center;
  }
  .front-brand {
    display: flex; align-items: center; gap: 30px;
  }
  .brand-dot {
    width: 110px; height: 110px; border-radius: 50%;
    background: var(--brand-blue-light);
    flex: none;
  }
  .brand-name {
    color: var(--white);
    font-weight: 700;
    font-size: 52px;
    line-height: 1.05;
    letter-spacing: 5px;
    text-transform: uppercase;
  }
  .card--back {
    top: 637px;
    background: linear-gradient(115deg, var(--card-dark-1) 0%, var(--card-dark-2) 70%);
  }
  .back-swoosh {
    position: absolute; inset: 0;
    width: 880px; height: 503px;
  }
  .back-brand {
    position: absolute;
    left: 612px; top: 178px;
    display: flex; align-items: center; gap: 14px;
  }
  .back-brand .brand-dot {
    width: 52px; height: 52px;
    background: var(--brand-blue);
  }
  .back-brand .brand-name {
    color: var(--ink);
    font-size: 24px;
    letter-spacing: 2px;
  }
  .contact {
    position: absolute;
    left: 62px; top: 58px;
    color: var(--white);
  }
  .contact__name {
    color: var(--brand-blue-light);
    font-weight: 700;
    font-size: 40px;
    line-height: 1;
  }
  .contact__title {
    font-size: 23px;
    letter-spacing: 1.5px;
    margin-top: 8px;
  }
  .contact__address {
    font-size: 23px;
    letter-spacing: 1.5px;
    line-height: 1.35;
    margin-top: 62px;
  }
  .contact__list {
    list-style: none;
    margin-top: 24px;
    font-size: 23px;
    letter-spacing: 1.5px;
    line-height: 1.4;
  }
  .contact__list li {
    display: flex; align-items: center; gap: 14px;
  }
  .contact__list svg {
    width: 20px; height: 20px; flex: none;
    fill: var(--brand-blue);
  }
</style>
</head>
<body>

<section class="card card--front" aria-label="Card front">
  <div class="front-brand">
    <span class="brand-dot"></span>
    <div class="brand-name">Quarrow<br>Signal Instruments</div>
  </div>
</section>

<section class="card card--back" aria-label="Card back">
  <svg class="back-swoosh" viewBox="0 0 880 503" aria-hidden="true">
    <path d="M478 0 C400 190 500 420 640 503 L880 503 L880 0 Z" fill="#ffffff"/>
    <path d="M486 0 C410 190 510 418 652 503 L880 503 L880 0 Z" fill="var(--brand-blue)"/>
    <path d="M502 0 C440 190 560 420 720 503 L880 503 L880 0 Z" fill="var(--band-dark)"/>
    <path d="M535 0 C470 200 590 420 760 480 L820 503 L880 503 L880 0 Z" fill="var(--paper)"/>
  </svg>

  <div class="back-brand">
    <span class="brand-dot"></span>
    <div class="brand-name">Quarrow<br>Signal Instruments</div>
  </div>

  <div class="contact">
    <p class="contact__name">Marlene</p>
    <p class="contact__title">Founder &amp; Director</p>
    <p class="contact__address">1180 Halvorsen Park Road.<br>Ridgeford, CO 80619</p>
    <ul class="contact__list">
      <li>
        <svg viewBox="0 0 24 24"><path d="M6.6 10.8a15.1 15.1 0 0 0 6.6 6.6l2.2-2.2a1 1 0 0 1 1-.25 11.4 11.4 0 0 0 3.6.57 1 1 0 0 1 1 1V20a1 1 0 0 1-1 1A17 17 0 0 1 3 4a1 1 0 0 1 1-1h3.5a1 1 0 0 1 1 1c0 1.25.2 2.45.57 3.57a1 1 0 0 1-.25 1z"/></svg>
        +001 555 218 3047
      </li>
      <li>
        <svg viewBox="0 0 24 24"><path d="M6 2h12v5H6zM4 8h16a2 2 0 0 1 2 2v7h-4v5H6v-5H2v-7a2 2 0 0 1 2-2zm4 8v4h8v-4z"/></svg>
        +001 555 218 3092
      </li>
      <li>
        <svg viewBox="0 0 24 24"><path d="M2 5h20v14H2zm2 2v.5l8 5 8-5V7l-8 5z"/></svg>
        info@quarrowsignal.com
      </li>
      <li>
        <svg viewBox="0 0 24 24"><path d="M12 2a10 10 0 1 0 0 20 10 10 0 0 0 0-20zm0 2c.9 0 2.3 1.9 2.8 5H9.2C9.7 5.9 11.1 4 12 4zM4.3 11h4.7a17 17 0 0 0 0 2H4.3a8 8 0 0 1 0-2zm10.7 0h4.7a8 8 0 0 1 0 2H15a17 17 0 0 0 0-2zm-5.8 4h5.6c-.5 3.1-1.9 5-2.8 5s-2.3-1.9-2.8-5z"/></svg>
        www.quarrowsignal.com
      </li>
    </ul>
  </div>
</section>

</body>
</html>
```